Modern Business Card

Modern professional business card with more than just logo and demographic info. Something memorable.

We are a trendy/modern chiropractic group with an emphasis on neurology, hence the minimalist-type brain logo. We want to convey that modern and technical aspect with professionalism and the elite nature of our practice environment.

```html
<!DOCTYPE html>
<html lang="en">
<head>
<meta charset="utf-8">
<title>Zentrilo Chiropractic – Business Card</title>
<link rel="stylesheet" href="https://fonts.googleapis.com/css2?family=Lora:wght@400&family=Quattrocento:wght@400&family=Khand:wght@600&display=swap">
<style>
  :root {
    --backdrop: #b4b4b4;
    --brand-blue: #3d5f98;
    --brand-blue-deep: #375789;
    --paper: #eeeeee;
    --ink: #2f2528;
    --edge: #3a2e32;
    --on-blue: #eef1f6;
    --on-blue-soft: #dfe5ef;
  }
  * { box-sizing: border-box; margin: 0; padding: 0; }
  html, body { width: 1200px; height: 576px; overflow: hidden; }
  body {
    background: var(--backdrop);
    position: relative;
    font-family: "Quattrocento", Georgia, serif;
  }
  .card {
    position: absolute;
    width: 484px;
    height: 292px;
    border-radius: 12px;
    overflow: hidden;
    box-shadow: 2px 3px 6px rgba(0,0,0,0.28);
  }

  /* Front */
  .card--front {
    left: 82px; top: 139px;
    background: linear-gradient(180deg, var(--brand-blue) 0%, var(--brand-blue-deep) 100%);
    display: flex; flex-direction: column; align-items: center; justify-content: center;
  }
  .front-name {
    font-family: "Lora", Georgia, serif;
    font-weight: 400;
    color: var(--on-blue);
    text-align: center;
    line-height: 1;
  }
  .front-name__main { display: block; font-size: 52px; letter-spacing: 1px; }
  .front-name__sub { display: block; font-size: 31px; letter-spacing: 0.5px; margin-top: 4px; }

  /* Back */
  .card--back { left: 602px; top: 138px; background: var(--paper); }
  .back-shape { position: absolute; inset: 0; }
  .brand {
    position: absolute; left: 24px; top: 123px;
    display: flex; align-items: center; gap: 8px;
  }
  .brand__mark { width: 14px; height: 14px; background: var(--brand-blue); flex: none; }
  .brand__name {
    font-family: "Lora", Georgia, serif;
    font-weight: 400;
    color: var(--ink);
    line-height: 0.95;
  }
  .brand__name span { display: block; }
  .brand__line1 { font-size: 23px; letter-spacing: 0.3px; }
  .brand__line2 { font-size: 15.5px; letter-spacing: 0.2px; }

  .contact { position: absolute; left: 277px; top: 68px; color: var(--on-blue); }
  .contact__name {
    font-family: "Khand", "Arial Narrow", sans-serif;
    font-weight: 600; font-size: 19px; line-height: 1.1;
  }
  .contact__title { font-size: 12px; color: var(--on-blue-soft); margin-top: 2px; }
  .contact__list { list-style: none; margin-top: 25px; font-size: 11.5px; }
  .contact__list li { display: flex; align-items: center; gap: 9px; height: 18.5px; }
  .contact__list svg { width: 10px; height: 10px; flex: none; fill: var(--on-blue); }
  .contact__address { font-size: 11.5px; line-height: 1.55; margin-top: 8px; }
</style>
</head>
<body>

  <section class="card card--front">
    <h1 class="front-name">
      <span class="front-name__main">ZENTRILO</span>
      <span class="front-name__sub">CHIROPRACTIC</span>
    </h1>
  </section>

  <section class="card card--back">
    <svg class="back-shape" viewBox="0 0 484 292" preserveAspectRatio="none" aria-hidden="true">
      <path d="M222 0 Q 282 146 226 292 L484 292 L484 0 Z" fill="var(--edge)"/>
      <path d="M229 0 Q 289 146 233 292 L484 292 L484 0 Z" fill="var(--brand-blue)"/>
    </svg>

    <div class="brand">
      <span class="brand__mark"></span>
      <p class="brand__name">
        <span class="brand__line1">ZENTRILO</span>
        <span class="brand__line2">CHIROPRACTIC</span>
      </p>
    </div>

    <div class="contact">
      <h2 class="contact__name">Marcus Reed Hale</h2>
      <p class="contact__title">Managing Director</p>
      <ul class="contact__list">
        <li>
          <svg viewBox="0 0 10 10"><path d="M0 3 Q5 -0.5 10 3 L10 4 L7.5 4 L7 3 L3 3 L2.5 4 L0 4 Z M2 5 L8 5 L9 9.5 L1 9.5 Z"/></svg>
          <span>555-014-2290</span>
        </li>
        <li>
          <svg viewBox="0 0 10 10"><path d="M0 2 L10 2 L10 8.5 L0 8.5 Z M0.8 2.8 L5 5.8 L9.2 2.8 Z" fill-rule="evenodd"/></svg>
          <span>marcus@zentrilo.example</span>
        </li>
        <li>
          <svg viewBox="0 0 10 10"><circle cx="5" cy="5" r="4.6"/><path d="M0.6 5 H9.4 M5 0.4 V9.6 M5 0.4 Q1.8 5 5 9.6 M5 0.4 Q8.2 5 5 9.6" stroke="var(--brand-blue)" stroke-width="0.8" fill="none"/></svg>
          <span>www.zentrilo.example</span>
        </li>
      </ul>
      <p class="contact__address">418 Sample Ave., Any City,<br>Any Town, US 123456</p>
    </div>
  </section>

</body>
</html>
```